Poster/flyer design needed for Choral Concert

Please include the following text:<br/>Title of Event: Voices in Bloom!<br/>Subtitle: A Choral Festival of Song to celebrate Kinship Fortnight<br/>Merrigang choirs come together to share their unique and beautiful music.<br/>Date: Sat March 21st 2020<br/>Time: 2pm - 4pm<br/>Venue: Pelmont Hall of Crafts<br/>Tickets: $10 each. Proceeds to Farmhand Trust & WBR Fire Corps<br/>Hosted By Lifted Tunes<br/>Featuring:<br/>Birrulee Unaccompanied Ladies' Choir<br/>Bread of Joy<br/>Merrigang Township Choir<br/>Chant Together<br/>* design required for A4 poster and DL flyer (may be modified)<br/>* Please use orange as the main colour<br/>* The Kinship fortnight logo must be included (see attached - either is fine). The frame may be useful as well.<br/>* Please include musical images<br/>* Visit kinshipfortnight.example.au for info on Kinship Fortnight

Target Market(s)

music-lovers, community-minded people, residents of the area, probably 30 + age

Industry/Entity Type

Entertainment

Font styles to use
Serif
Sans Serif

Colors
f78f20
ffffff

Requirements
Must have
• Orange colour
• Kinship logo
• required text
Nice to have
• A musical theme
Should not have
• writing should not be too small and difficult to read

```html
<!DOCTYPE html>
<html lang="en">
<head>
<meta charset="utf-8">
<title>Voices in Bloom! – Kinship Fortnight Choral Festival</title>
<link rel="stylesheet" href="https://fonts.googleapis.com/css2?family=Anton&family=Comfortaa:wght@500;700&family=Oswald:wght@400;500;600&family=Parisienne&display=swap">
<style>
  :root {
    --orange: #f78f20;
    --orange-light: #f9a032;
    --orange-deep: #e0742a;
    --brown: #6b2a12;
    --brown-box: #6a2513;
    --brown-dark: #4a1c0c;
    --white: #ffffff;
    --ink: #111111;
  }
  * { margin: 0; padding: 0; box-sizing: border-box; }
  html, body { width: 871px; height: 1200px; overflow: hidden; background: var(--white); }
  .poster {
    position: relative;
    width: 871px;
    height: 1200px;
    overflow: hidden;
    background: linear-gradient(180deg, #c56a25 0%, #e07f25 40%, var(--orange) 62%, var(--orange-light) 100%);
    font-family: "Oswald", sans-serif;
  }
  .choir-photo {
    position: absolute;
    left: 0; top: 0;
    width: 871px; height: 680px;
    background:
      radial-gradient(ellipse at 70% 30%, rgba(90,45,20,0.55), transparent 60%),
      radial-gradient(ellipse at 25% 55%, rgba(110,55,25,0.45), transparent 55%),
      linear-gradient(180deg, rgba(120,60,25,0.7) 0%, rgba(200,110,40,0.35) 70%, rgba(247,143,32,0) 100%);
  }
  .brand-mark {
    position: absolute;
    left: 78px; top: 82px;
    font-family: "Oswald", sans-serif;
    font-weight: 500;
    font-size: 30px;
    letter-spacing: 0.5px;
    color: var(--white);
  }
  .title-big {
    position: absolute;
    left: 0; width: 871px; top: 400px;
    text-align: center;
    font-family: "Anton", sans-serif;
    font-size: 252px;
    line-height: 1;
    letter-spacing: 2px;
    background: linear-gradient(180deg, #7a3416 10%, #b8501f 55%, var(--orange-deep) 100%);
    -webkit-background-clip: text;
    background-clip: text;
    color: transparent;
  }
  .title-script {
    position: absolute;
    left: 0; width: 871px; top: 330px;
    text-align: center;
    font-family: "Parisienne", cursive;
    font-size: 132px;
    line-height: 1;
    color: var(--white);
  }
  .subtitle {
    position: absolute;
    left: 0; width: 871px; top: 648px;
    text-align: center;
    font-family: "Oswald", sans-serif;
    font-weight: 500;
    font-size: 33px;
    line-height: 36px;
    color: var(--brown);
    text-transform: uppercase;
  }
  .lineup {
    position: absolute;
    left: 30px; width: 432px; top: 808px;
    text-align: center;
    color: var(--brown-dark);
    text-transform: uppercase;
  }
  .lineup .label { font-size: 18px; font-weight: 400; line-height: 22px; color: var(--brown); }
  .lineup .host { font-size: 25px; font-weight: 400; line-height: 30px; margin-bottom: 18px; }
  .lineup ul { list-style: none; }
  .lineup li { font-size: 23px; line-height: 35px; }
  .lineup li::before {
    content: "";
    display: inline-block;
    width: 0; height: 0;
    border-left: 6px solid var(--brown-dark);
    border-top: 5px solid transparent;
    border-bottom: 5px solid transparent;
    margin-right: 8px;
    vertical-align: 5px;
  }
  .event-box {
    position: absolute;
    left: 445px; top: 795px;
    width: 356px; height: 180px;
    background: var(--brown-box);
    color: var(--white);
    display: flex; flex-direction: column; justify-content: center; align-items: center;
    font-family: "Oswald", sans-serif;
    font-weight: 600;
    font-size: 31px;
    line-height: 38px;
    text-transform: uppercase;
    text-align: center;
  }
  .event-box sup { font-size: 16px; vertical-align: 14px; }
  .tickets {
    position: absolute;
    left: 445px; width: 356px; top: 1000px;
    text-align: center;
    color: var(--brown-dark);
    font-family: "Comfortaa", sans-serif;
  }
  .tickets .price { font-weight: 700; font-size: 23px; line-height: 28px; text-transform: uppercase; }
  .tickets .proceeds { font-weight: 500; font-size: 15px; line-height: 19px; }
  .partner-band {
    position: absolute;
    left: 0; top: 1109px;
    width: 871px; height: 91px;
    background: var(--white);
    display: flex; align-items: center; justify-content: space-around;
    padding: 0 90px;
    color: var(--ink);
    font-family: "Oswald", sans-serif;
  }
  .partner-office { font-size: 17px; font-weight: 500; display: flex; align-items: center; gap: 8px; }
  .partner-office .square { width: 22px; height: 22px; background: var(--ink); }
  .partner-tagline { font-size: 24px; font-weight: 400; letter-spacing: 0.5px; }
  .partner-hashtag { font-size: 24px; font-weight: 600; }
</style>
</head>
<body>
<main class="poster">
  <div class="choir-photo" role="img" aria-label="Photo of a choir in formal black attire standing in rows, tinted orange"></div>

  <div class="brand-mark">KINSHIP FORTNIGHT</div>

  <h1>
    <span class="title-big">BLOOM</span>
    <span class="title-script">Voices in</span>
  </h1>

  <p class="subtitle">
    A choral festival of song to celebrate Kinship Fortnight<br>
    Merrigang choirs come together to share<br>
    their unique and beautiful music.
  </p>

  <section class="lineup">
    <p class="label">Hosted by:</p>
    <p class="host">Lifted Tunes</p>
    <p class="label">Featuring:</p>
    <ul>
      <li>Birrulee Unaccompanied Ladies' Choir</li>
      <li>Bread of Joy</li>
      <li>Merrigang Township Choir</li>
      <li>Chant Together</li>
    </ul>
  </section>

  <section class="event-box">
    <p>Saturday, March 21<sup>st</sup></p>
    <p>Pelmont Hall of Crafts</p>
    <p>2pm - 4pm</p>
  </section>

  <section class="tickets">
    <p class="price">Tickets: $10 each</p>
    <p class="proceeds">Proceeds to Farmhand Trust<br>&amp; WBR Fire Corps</p>
  </section>

  <footer class="partner-band">
    <div class="partner-office"><span class="square"></span>Civic Unity Office</div>
    <div class="partner-tagline">ALL TOGETHER HERE</div>
    <div class="partner-hashtag">#kinshipfortnight</div>
  </footer>
</main>
</body>
</html>
```